Eye Catching Business Card for Optometrist

We've recently refreshed our logo and now we need a fresh and bold look for our business cards. We provide progressive ways to improve people's vision and protect their eye health.

Use our new logo as guidance into the colors to use. As far as style goes, I love how bold and eye catching the card is for Lanternfield Studio. Feel free to use your creative judgement.

Tagline: "Bright sight for the whole family."

pertinent info to include:

Dr. Marcus Velbrin
Optometrist

7258 Dunmore Ridge Blvd #215
Brantwell, MO 64172
(555) 382-9017

marc@brantwellfamilyeyecare.example
www.brantwellfamilyeyecare.example

```html
<!DOCTYPE html>
<html lang="en">
<head>
<meta charset="utf-8">
<title>Brantwell Family Eye Care – Business Card</title>
<link rel="stylesheet" href="https://fonts.googleapis.com/css2?family=Open+Sans:wght@300;700&family=Josefin+Sans:wght@700&family=Arimo:wght@400&display=swap">
<style>
  :root {
    --brand-red: #a3131f;
    --card-grey-light: #9a9a98;
    --card-grey-dark: #7f807e;
    --sheet-white: #ffffff;
    --sheet-border: #555555;
    --text-white: #ffffff;
  }
  html, body {
    margin: 0;
    padding: 0;
    width: 1200px;
    height: 1000px;
    overflow: hidden;
    background: var(--sheet-white);
  }
  .sheet {
    position: relative;
    width: 1200px;
    height: 1000px;
    box-sizing: border-box;
    border: 1px solid var(--sheet-border);
    background: var(--sheet-white);
    overflow: hidden;
  }
  .accent-bar {
    position: absolute;
    background: var(--brand-red);
  }
  .accent-bar--top-right { left: 1168px; top: 0; width: 32px; height: 185px; }
  .accent-bar--bottom-left { left: 0; top: 818px; width: 32px; height: 182px; }

  .card {
    position: absolute;
    left: 262px;
    width: 678px;
    height: 412px;
    background: radial-gradient(ellipse at 45% 40%, var(--card-grey-light), var(--card-grey-dark));
  }
  .card--front { top: 68px; }
  .card--back { top: 522px; }

  .practice-name {
    position: absolute;
    left: 0;
    width: 100%;
    top: 232px;
    margin: 0;
    text-align: center;
    font-family: "Open Sans", sans-serif;
    font-weight: 700;
    font-size: 38px;
    letter-spacing: 1px;
    text-transform: uppercase;
    color: var(--brand-red);
  }
  .tagline {
    position: absolute;
    left: 0;
    width: 100%;
    top: 322px;
    margin: 0;
    text-align: center;
    font-family: "Open Sans", sans-serif;
    font-weight: 300;
    font-size: 29px;
    color: var(--text-white);
  }

  .doctor-name {
    position: absolute;
    left: 0;
    width: 100%;
    top: 64px;
    margin: 0;
    text-align: center;
    font-family: "Josefin Sans", sans-serif;
    font-weight: 700;
    font-size: 43px;
    letter-spacing: 1px;
    text-transform: uppercase;
    color: var(--brand-red);
  }
  .doctor-title {
    position: absolute;
    left: 0;
    width: 100%;
    top: 114px;
    margin: 0;
    text-align: center;
    font-family: "Arimo", sans-serif;
    font-size: 32px;
    color: var(--text-white);
  }

  .contact-list {
    position: absolute;
    left: 140px;
    top: 216px;
    margin: 0;
    padding: 0;
    list-style: none;
    font-family: "Arimo", sans-serif;
    font-size: 22px;
    line-height: 27px;
    color: var(--text-white);
  }
  .contact-item {
    position: relative;
    padding-left: 52px;
    margin-bottom: 12px;
  }
  .contact-icon {
    position: absolute;
    left: 0;
    top: 1px;
    width: 26px;
    height: 26px;
    fill: none;
    stroke: var(--brand-red);
    stroke-width: 2;
  }
  .contact-icon .solid { fill: var(--brand-red); stroke: none; }
</style>
</head>
<body>
<main class="sheet">
  <div class="accent-bar accent-bar--top-right"></div>
  <div class="accent-bar accent-bar--bottom-left"></div>

  <section class="card card--front" aria-label="Card front with practice name">
    <h1 class="practice-name">Brantwell Family Eye Care</h1>
    <p class="tagline">Bright sight for the whole family</p>
  </section>

  <section class="card card--back" aria-label="Card back with contact details">
    <h2 class="doctor-name">Dr. Marcus Velbrin</h2>
    <p class="doctor-title">Optometrist</p>

    <ul class="contact-list">
      <li class="contact-item">
        <svg class="contact-icon" viewBox="0 0 26 26" aria-hidden="true">
          <path class="solid" d="M7 3 l4 5 -2.5 2.5 c1.5 3 3.5 5 6.5 6.5 L17.5 14.5 l5 4 -2.5 3.5 C11 21 5 15 4 6 Z"/>
        </svg>
        (555) 382-9017
      </li>
      <li class="contact-item">
        <svg class="contact-icon" viewBox="0 0 26 26" aria-hidden="true">
          <circle cx="13" cy="13" r="10"/>
          <ellipse cx="13" cy="13" rx="4.5" ry="10"/>
          <line x1="3" y1="13" x2="23" y2="13"/>
          <line x1="5" y1="8" x2="21" y2="8"/>
          <line x1="5" y1="18" x2="21" y2="18"/>
        </svg>
        www.brantwellfamilyeyecare.example
      </li>
      <li class="contact-item">
        <svg class="contact-icon" viewBox="0 0 26 26" aria-hidden="true">
          <rect x="2" y="6" width="22" height="15"/>
          <polyline points="2,6 13,15 24,6"/>
          <line x1="2" y1="21" x2="10" y2="13"/>
          <line x1="24" y1="21" x2="16" y2="13"/>
        </svg>
        marc@brantwellfamilyeyecare.example
      </li>
      <li class="contact-item">
        <svg class="contact-icon" viewBox="0 0 26 26" aria-hidden="true">
          <path class="solid" d="M13 1 C7.5 1 4 5 4 10 c0 6 9 15 9 15 s9-9 9-15 C22 5 18.5 1 13 1 Z M13 6 a4 4 0 1 1 0 8 a4 4 0 1 1 0-8 Z" fill-rule="evenodd"/>
        </svg>
        7258 Dunmore Ridge Blvd #215<br>
        Brantwell, MO 64172
      </li>
    </ul>
  </section>
</main>
</body>
</html>
```